Tech business card design

We need an amazing business card design for our new business 'Pexla' a marketing tech startup based in Sydney, Australia. We provide an online marketplace for businesses to search and buy advertising media, connect with service providers and learn more about marketing. We wish to communicate 'cool tech', reliability and professionalism and design based around our logo.

Target Market(s)

Business Owners

Contact Information for Business Card

Name
Position
Email Address
Website
Phone Number

Font styles to use
Other font styles liked:
• Avenir & Avenir Next

Colors

Designer to choose colors to be used in the design.

```html
<!DOCTYPE html>
<html lang="en">
<head>
<meta charset="utf-8">
<title>Pexla Business Card</title>
<link rel="stylesheet" href="https://fonts.googleapis.com/css2?family=Work+Sans:wght@400;500;700&family=Oswald:wght@500&display=swap">
<style>
  :root {
    --backdrop: #151515;
    --card: #1d1d1d;
    --card-edge: #262626;
    --ink-gloss: #0c0c0c;
    --ink-soft: #2e2e2e;
    --ink-light: #e4e4e4;
    --logo: #d6d6d6;
    --rule: #4a4a4a;
  }
  * { margin: 0; padding: 0; box-sizing: border-box; }
  html, body {
    width: 1200px;
    height: 900px;
    overflow: hidden;
    background: var(--backdrop);
    font-family: "Work Sans", Arial, sans-serif;
  }
  .stage {
    position: relative;
    width: 1200px;
    height: 900px;
  }
  .card {
    position: absolute;
    left: 320px;
    width: 560px;
    height: 320px;
    background: var(--card);
    border: 1px solid var(--card-edge);
  }
  .card--front { top: 110px; }
  .card--back { top: 470px; }

  .brand-name {
    position: absolute;
    left: 0;
    right: 0;
    top: 112px;
    text-align: center;
    font-weight: 700;
    font-size: 84px;
    line-height: 1;
    letter-spacing: -2px;
    color: var(--logo);
  }

  .person {
    position: absolute;
    right: 320px;
    top: 112px;
    text-align: right;
  }
  .person__name {
    font-family: "Oswald", "Arial Narrow", sans-serif;
    font-weight: 500;
    font-size: 25px;
    line-height: 1.05;
    letter-spacing: -0.5px;
    text-transform: uppercase;
    color: var(--ink-gloss);
    white-space: nowrap;
  }
  .person__role {
    font-size: 13px;
    letter-spacing: 1.5px;
    color: var(--ink-soft);
    margin-top: 2px;
  }
  .divider {
    position: absolute;
    left: 258px;
    top: 108px;
    width: 1px;
    height: 66px;
    background: var(--rule);
  }
  .contact-list {
    position: absolute;
    left: 284px;
    top: 110px;
    list-style: none;
  }
  .contact-list__item {
    display: flex;
    align-items: center;
    gap: 12px;
    height: 22px;
    font-size: 15px;
    letter-spacing: 1px;
    color: var(--ink-light);
  }
  .contact-list__icon {
    width: 11px;
    height: 11px;
    flex: none;
  }
  .address {
    position: absolute;
    left: 70px;
    bottom: 44px;
    font-size: 15px;
    letter-spacing: 1px;
    color: var(--ink-gloss);
  }
</style>
</head>
<body>
<main class="stage">
  <section class="card card--front" aria-label="Card front">
    <div class="brand-name">Pexla</div>
  </section>

  <section class="card card--back" aria-label="Card back">
    <div class="person">
      <div class="person__name">Daniel Hart</div>
      <div class="person__role">Director</div>
    </div>
    <div class="divider"></div>
    <ul class="contact-list">
      <li class="contact-list__item">
        <svg class="contact-list__icon" viewBox="0 0 12 12" aria-hidden="true">
          <path d="M2.5 1 L4.5 1 L5.3 3.5 L4 4.6 Q5 7 7.4 8 L8.5 6.7 L11 7.5 L11 9.5 Q10.5 11 9 11 Q1 10 1 3 Q1 1.5 2.5 1 Z" fill="var(--ink-light)"/>
        </svg>
        <span>+61 2 4821 7390</span>
      </li>
      <li class="contact-list__item">
        <svg class="contact-list__icon" viewBox="0 0 12 12" aria-hidden="true">
          <rect x="0.8" y="2.3" width="10.4" height="7.4" fill="none" stroke="var(--ink-light)" stroke-width="1.2"/>
          <path d="M1 2.6 L6 6.6 L11 2.6" fill="none" stroke="var(--ink-light)" stroke-width="1.2"/>
        </svg>
        <span>info@pexla.com</span>
      </li>
      <li class="contact-list__item">
        <svg class="contact-list__icon" viewBox="0 0 12 12" aria-hidden="true">
          <g fill="none" stroke="var(--ink-light)" stroke-width="1">
            <circle cx="6" cy="6" r="5"/>
            <ellipse cx="6" cy="6" rx="2.2" ry="5"/>
            <path d="M1 6 H11 M1.8 3.5 H10.2 M1.8 8.5 H10.2"/>
          </g>
        </svg>
        <span>www.pexla.com</span>
      </li>
    </ul>
    <div class="address">218 Kent Street Sydney, NSW 2000</div>
  </section>
</main>
</body>
</html>
```